Business Card Design Project

use presentation folder design and my logo and make 4 over 4 business cards

Industry/Entity Type

Business

Requirements
Must have
• use the design from my presentation folder and put my logo on it

Name
Title
phone
fax
email

```html
<!DOCTYPE html>
<html lang="en">
<head>
<meta charset="utf-8">
<title>KindPath Counseling – Business Cards</title>
<link href="https://fonts.googleapis.com/css2?family=Lora:wght@400;700&family=Montserrat:wght@400&display=swap" rel="stylesheet">
<style>
  :root{
    --stage:#e9e7e4;
    --card-white:#ffffff;
    --panel-light:#eef1f7;
    --tile-gray:#d3d4d6;
    --tile-sand:#ddd5c4;
    --tile-sand-deep:#d7cfbb;
    --tile-brown:#7a4a23;
    --brand-brown:#8a5424;
    --ink:#2b2b2b;
    --ink-soft:#555555;
    --back-cream:#ede3d9;
  }
  *{box-sizing:border-box;margin:0;padding:0}
  html,body{width:1200px;height:900px;overflow:hidden}
  body{background:var(--stage);position:relative;font-family:"Lora",Georgia,serif}

  .card{position:absolute;width:560px;height:320px;border-radius:4px;overflow:hidden;
        box-shadow:0 6px 18px rgba(0,0,0,.12)}
  .card--front{left:60px;top:110px;background:var(--card-white)}
  .card--back{left:580px;top:470px;background:var(--back-cream)}

  .tile{position:absolute;border-radius:16px}
  .tile--gray{left:-16px;top:-16px;width:206px;height:126px;background:var(--tile-gray)}
  .tile--sand-top{left:204px;top:-16px;width:120px;height:70px;background:var(--tile-sand)}
  .tile--sand-big{left:204px;top:194px;width:250px;height:142px;background:var(--tile-sand-deep)}
  .tile--brown{left:468px;top:194px;width:108px;height:142px;background:var(--tile-brown)}
  .panel{position:absolute;border-radius:16px;background:var(--panel-light)}
  .panel--logo{left:-16px;top:124px;width:206px;height:212px}
  .panel--contact{left:338px;top:-16px;width:238px;height:196px}
  .panel--mid{left:204px;top:68px;width:120px;height:112px}

  .brand{position:absolute;left:14px;top:178px;width:170px;text-align:center;color:var(--brand-brown)}
  .brand__name{font-family:"Lora",Georgia,serif;font-weight:400;font-size:28px;line-height:1}
  .brand__sub{font-family:"Montserrat",Arial,sans-serif;font-size:9px;letter-spacing:4px;margin-top:6px}
  .brand__tag{font-family:"Montserrat",Arial,sans-serif;font-size:9px;color:var(--ink-soft);margin-top:4px}

  .contact{position:absolute;left:354px;top:22px;width:200px}
  .contact__name{font-weight:700;font-size:19px;color:var(--brand-brown)}
  .contact__title{font-size:12px;color:var(--ink);margin-bottom:14px}
  .contact__row{display:flex;align-items:center;gap:8px;font-size:11.5px;color:var(--ink);line-height:19px}
  .contact__row--web{font-weight:700}
  .contact__icon{width:13px;height:13px;flex:none}

  .back__brand{position:absolute;left:0;right:0;top:104px;text-align:center;color:var(--brand-brown)}
  .back__name{font-family:"Lora",Georgia,serif;font-weight:400;font-size:40px;line-height:1}
  .back__sub{font-family:"Montserrat",Arial,sans-serif;font-size:11px;letter-spacing:6px;margin-top:8px}
  .back__tag{font-family:"Montserrat",Arial,sans-serif;font-size:11px;color:var(--ink-soft);margin-top:4px}
  .back__rule{width:220px;height:1px;background:var(--brand-brown);margin:12px auto}
  .back__web{font-family:"Lora",Georgia,serif;font-size:16px}
</style>
</head>
<body>

<section class="card card--front" aria-label="Business card front">
  <div class="tile tile--gray"></div>
  <div class="tile tile--sand-top"></div>
  <div class="panel panel--mid"></div>
  <div class="tile tile--sand-big"></div>
  <div class="tile tile--brown"></div>
  <div class="panel panel--logo"></div>
  <div class="panel panel--contact"></div>

  <div class="brand">
    <div class="brand__name">KindPath</div>
    <div class="brand__sub">COUNSELING</div>
    <div class="brand__tag">a steady path to recovery</div>
  </div>

  <div class="contact">
    <div class="contact__name">Mara Ellison</div>
    <div class="contact__title">Director</div>
    <div class="contact__row">
      <svg class="contact__icon" viewBox="0 0 14 14"><circle cx="7" cy="7" r="6.3" fill="none" stroke="#8a5424" stroke-width="1"/><path d="M4.6 4.2l1.3-.4.8 1.6-.8.6c.4.9 1 1.5 1.9 1.9l.6-.8 1.6.8-.4 1.3c-2.6.1-5.1-2.4-5-5z" fill="#8a5424"/></svg>
      <span>555. 0142. 310</span>
    </div>
    <div class="contact__row">
      <svg class="contact__icon" viewBox="0 0 14 14"><circle cx="7" cy="7" r="6.3" fill="none" stroke="#8a5424" stroke-width="1"/><rect x="4" y="5.5" width="6" height="4" fill="#8a5424"/><rect x="5" y="3.6" width="4" height="2" fill="none" stroke="#8a5424" stroke-width=".8"/></svg>
      <span>555. 0142. 311</span>
    </div>
    <div class="contact__row">
      <svg class="contact__icon" viewBox="0 0 14 14"><circle cx="7" cy="7" r="6.3" fill="none" stroke="#8a5424" stroke-width="1"/><rect x="3.8" y="4.8" width="6.4" height="4.4" fill="none" stroke="#8a5424" stroke-width=".9"/><path d="M3.8 4.8L7 7.4l3.2-2.6" fill="none" stroke="#8a5424" stroke-width=".9"/></svg>
      <span>m.ellison@kindpath.com</span>
    </div>
    <div class="contact__row contact__row--web">
      <svg class="contact__icon" viewBox="0 0 14 14"><circle cx="7" cy="7" r="6.3" fill="none" stroke="#8a5424" stroke-width="1"/><circle cx="7" cy="7" r="3.4" fill="none" stroke="#8a5424" stroke-width=".9"/><path d="M3.6 7h6.8M7 3.6v6.8" stroke="#8a5424" stroke-width=".7"/></svg>
      <span>www.kindpath.com</span>
    </div>
  </div>
</section>

<section class="card card--back" aria-label="Business card back">
  <div class="back__brand">
    <div class="back__name">KindPath</div>
    <div class="back__sub">COUNSELING</div>
    <div class="back__tag">a steady path to recovery</div>
    <div class="back__rule"></div>
    <div class="back__web">www.kindpath.com</div>
  </div>
</section>

</body>
</html>
```